home accents e-commerce website

I'd like a professional simple website designed where I can sell my home goods. I already have my domain name registered. I need the website to accept credit card payments and Monvex. It should have a shopping cart option and calculate sales tax and shipping costs on merchandise automatically.

I'll be taking photographs of the merchandise and writing product descriptions myself. (I'm not a professional photographer, so these photos probably won't look too polished. If you can help me make them look better, that'd be great). As I add new merchandise in the future, I'd like an option where I can log in to the back end myself and add pictures/product descriptions. And take old products down as they sell out. So the website needs to be user-friendly for me, even though I'm completely web design illiterate!

I'd like a creative, talented person who can create a whimsical, cute website. Nothing too corporate-looking.

Thank you!

Target Market(s)

women, online shoppers, New York City-area, (ship products to the United States only)

Industry/Entity Type

Home And Garden

Coding

Coded - Design and coding required

Number of Pages Required

1 page

Font styles to use
Sans Serif

Colors
0355a3
ffffff

Requirements
Must have
• shopping cart feature
• safe, secure credit card and Monvex payments
• ability for me to go in and add new products and take down old/sold products
Nice to have
• whimsical, cute design
Should not have
• too corporate-looking

```html
<!DOCTYPE html>
<html lang="en">
<head>
<meta charset="utf-8">
<title>Lumora Home Goods</title>
<link href="https://fonts.googleapis.com/css2?family=Nunito+Sans:wght@400;600;700;800&display=swap" rel="stylesheet">
<style>
:root{
  --brand:#0355a3;
  --white:#ffffff;
  --ink:#2b2b2b;
  --muted:#777777;
  --topbar:#333333;
  --line:#e2e2e2;
  --panel:rgba(30,30,30,.86);
  --tile:#f4f4f4;
  --star:#8a7f6a;
}
*{box-sizing:border-box;margin:0;padding:0}
html,body{width:1200px;height:2500px;overflow:hidden;background:var(--white)}
body{position:relative;font-family:"Nunito Sans",Arial,sans-serif;color:var(--ink)}
.abs{position:absolute}
a{color:inherit;text-decoration:none}

/* top bar */
.topbar{left:0;top:0;width:1200px;height:47px;background:var(--topbar);color:var(--white);font-size:13px}
.topbar .contact{left:98px;top:14px;display:flex;gap:12px;align-items:center}
.topbar .account{right:100px;top:14px;display:flex;gap:12px;align-items:center}
.topbar svg{vertical-align:-2px;margin-right:6px}

/* header */
.logo{left:98px;top:54px;width:180px;text-align:center;color:var(--brand)}
.logo .name{font-size:42px;font-weight:800;letter-spacing:1px;line-height:46px}
.logo .tag{font-size:13px;letter-spacing:4px;font-weight:600}
.search{left:445px;top:58px;width:372px;height:42px;border:1px solid #cfcfcf;font-size:12px;color:#999;padding:13px 14px}
.search svg{position:absolute;right:14px;top:12px}
.social-top{left:847px;top:60px;display:flex;gap:8px}
.social-top span{width:38px;height:38px;border-radius:50%;background:var(--brand)}
.social-top span:nth-child(2){background:#2c9ad6}
.social-top span:nth-child(3){background:#7d6a5b}
.social-top span:nth-child(4){background:#c9232d}
.cart-top{left:1062px;top:60px}

/* nav */
.navline{left:0;top:127px;width:1200px;height:45px;border-top:1px solid var(--line)}
.categories{left:98px;top:127px;width:287px;height:45px;background:var(--brand);color:var(--white);font-weight:700;font-size:18px;padding:11px 20px;display:flex;align-items:center;gap:26px}
.mainnav{top:138px;font-size:15px;font-weight:600;color:var(--ink)}
.mainnav.active{color:var(--brand)}

/* hero */
.hero{left:0;top:172px;width:1200px;height:486px;background:linear-gradient(180deg,#e9e8e4 0%,#dcdad3 62%,#c9c5bb 100%)}
.hero-art{left:0;top:400px;width:1200px;height:258px;background:linear-gradient(90deg,#e2d86a 0%,#e37e84 25%,#7cc6d8 40%,#f2e66a 52%,#e9c65c 62%,#e07c82 72%,#46aeb6 86%,#eee07a 100%);opacity:.85}
.hero-floor{left:0;top:600px;width:1200px;height:58px;background:#d4d0c8}
.hero-title{left:0;top:238px;width:1200px;text-align:center;font-size:50px;line-height:60px;font-weight:600;letter-spacing:1px;color:#2a2a2a}
.hero-sub{left:0;top:308px;width:1200px;text-align:center;font-size:20px;color:#444}
.hero-btn{left:523px;top:358px;width:155px;height:49px;border:1px solid #8a8a8a;border-radius:4px;color:var(--brand);font-weight:800;font-size:16px;text-align:center;line-height:47px;background:rgba(255,255,255,.35)}
.hero-arrow{top:393px;width:36px;height:40px;background:rgba(120,120,120,.55)}
.catpanel{left:98px;top:172px;width:287px;height:486px}
.catlist{left:134px;top:198px;list-style:none;color:var(--white);font-size:15px;font-weight:600}
.catlist li{height:44.7px;display:flex;align-items:center;gap:12px}

/* products */
.section-title{left:0;top:732px;width:1200px;text-align:center;font-size:32px;font-weight:700;color:#222}
.product{width:230px}
.product .photo{width:230px;height:247px;background:var(--tile);position:relative}
.product .photo .fill{position:absolute;left:30px;top:40px;width:170px;height:167px;border-radius:12px}
.product h3{margin-top:28px;font-size:17px;font-weight:600;color:#333}
.product p{margin-top:10px;font-size:12px;line-height:20px;color:var(--muted)}
.product .meta{margin-top:12px;display:flex;justify-content:space-between;align-items:center}
.product .price{color:var(--brand);font-weight:800;font-size:16px}
.product .stars{color:var(--star);font-size:12px;letter-spacing:1px}
.photo.hover{background:#4a7fbf}
.photo.hover .fill{opacity:.6}
.hover-icons{position:absolute;left:90px;top:36px;display:flex;flex-direction:column;gap:10px}
.hover-icons span{width:50px;height:50px;border:1px solid rgba(255,255,255,.75);border-radius:50%;display:flex;align-items:center;justify-content:center}

.more-btn{left:495px;top:1745px;width:210px;height:47px;border:1px solid #c8c8c8;border-radius:4px;text-align:center;line-height:45px;color:var(--brand);font-weight:800;font-size:15px}

/* promo banners */
.promo{top:1890px;height:215px;overflow:hidden}
.promo .art{position:absolute;inset:0}
.promo .copy{position:absolute}
.promo .big{font-size:34px;font-weight:800;color:#1f1f1f;letter-spacing:.5px}
.promo .small{font-size:22px;color:#1f1f1f}
.promo .mid{font-size:26px;font-weight:800;color:#1f1f1f}
.promo .btn{display:inline-block;margin-top:22px;border:1px solid #555;border-radius:4px;padding:6px 18px;color:var(--brand);font-weight:800;font-size:14px;background:rgba(255,255,255,.35)}

/* footer */
.fcol{top:2195px}
.fcol h4{font-size:18px;font-weight:700;color:#222;margin-bottom:18px}
.fcol ul{list-style:none;font-size:12px;color:#555}
.fcol li{height:27.5px}
.fdivider{top:2195px;width:1px;height:200px;background:var(--line)}
.newsletter p{font-size:12px;color:#555;margin-bottom:14px}
.subscribe{display:flex;height:36px}
.subscribe .field{width:228px;border:1px solid #cfcfcf;font-size:12px;color:#777;padding:10px 12px}
.subscribe .go{width:92px;background:var(--brand);color:var(--white);font-size:13px;font-weight:800;text-align:center;line-height:36px}
.newsletter h5{font-size:18px;font-weight:600;color:#222;margin:16px 0 10px}
.social-foot{display:flex;gap:8px}
.social-foot span{width:34px;height:34px;border-radius:50%;background:var(--brand)}
.social-foot span:nth-child(odd){background:#2c9ad6}
.social-foot span:nth-child(3n){background:#c9232d}
.bottomline{left:98px;top:2427px;width:1004px;height:1px;background:var(--line)}
.copyright{left:95px;top:2454px;font-size:12px;color:#555}
.payments{left:850px;top:2447px;display:flex;gap:6px}
.payments span{height:28px;padding:0 6px;border:1px solid #cfcfcf;border-radius:3px;font-size:10px;font-weight:700;color:var(--ink);line-height:26px}
</style>
</head>
<body>

<!-- top bar -->
<div class="abs topbar">
  <div class="abs contact">
    <span><svg width="12" height="12" viewBox="0 0 24 24"><path fill="#fff" d="M6.6 10.8a15 15 0 0 0 6.6 6.6l2.2-2.2c.3-.3.7-.4 1-.2 1.1.4 2.3.6 3.6.6.6 0 1 .4 1 1V20c0 .6-.4 1-1 1A17 17 0 0 1 3 4c0-.6.4-1 1-1h3.5c.6 0 1 .4 1 1 0 1.3.2 2.5.6 3.6.1.3 0 .7-.2 1z"/></svg>1 555 010 0199</span>
    <span>|</span>
    <span><svg width="13" height="11" viewBox="0 0 24 18"><rect width="24" height="18" rx="2" fill="#fff"/><path d="M1 1l11 9 11-9" stroke="#333" stroke-width="2" fill="none"/></svg>info@lumora.com</span>
  </div>
  <div class="abs account">
    <span><svg width="13" height="11" viewBox="0 0 24 20"><path d="M2 6h18l-4-4M22 14H4l4 4" stroke="#fff" stroke-width="2.5" fill="none"/></svg>Compare</span><span>|</span>
    <span><svg width="11" height="12" viewBox="0 0 20 22"><circle cx="10" cy="6" r="5" fill="#fff"/><path d="M0 22c0-6 4-9 10-9s10 3 10 9z" fill="#fff"/></svg>My Account</span><span>|</span>
    <span><svg width="10" height="12" viewBox="0 0 18 22"><rect y="9" width="18" height="13" rx="2" fill="#fff"/><path d="M4 9V6a5 5 0 0 1 10 0v3" stroke="#fff" stroke-width="3" fill="none"/></svg>Login</span><span>|</span>
    <span><svg width="15" height="12" viewBox="0 0 28 22"><circle cx="9" cy="6" r="5" fill="#fff"/><circle cx="20" cy="6" r="4" fill="#fff"/><path d="M0 22c0-6 3-9 9-9s9 3 9 9zM18 13c6 0 10 3 10 9h-8z" fill="#fff"/></svg>Join</span>
  </div>
</div>

<!-- header -->
<div class="abs logo"><div class="name">lumora</div><div class="tag">HOME GOODS</div></div>
<div class="abs search">Search Products
  <svg width="16" height="16" viewBox="0 0 24 24"><circle cx="10" cy="10" r="7" stroke="#666" stroke-width="2.5" fill="none"/><path d="M15 15l7 7" stroke="#666" stroke-width="2.5"/></svg>
</div>
<div class="abs social-top" role="img" aria-label="Social network links"><span></span><span></span><span></span><span></span></div>
<svg class="abs cart-top" width="34" height="32" viewBox="0 0 34 32" role="img" aria-label="Shopping cart"><path d="M1 3h6l4 18h18l4-13H9" stroke="#0355a3" stroke-width="3" fill="none" stroke-linejoin="round"/><path d="M11 9h20l-3 9H13z" fill="#0355a3"/><circle cx="13" cy="27" r="3" fill="#0355a3"/><circle cx="27" cy="27" r="3" fill="#0355a3"/></svg>

<!-- nav -->
<div class="abs navline"></div>

<!-- hero -->
<div class="abs hero"></div>
<div class="abs hero-art" role="img" aria-label="Row of colourful patterned throw pillows on a white sofa"></div>
<div class="abs hero-floor" role="img" aria-label="Whitewashed wooden floor"></div>
<div class="abs hero-arrow" style="left:0"><svg width="36" height="40" viewBox="0 0 36 40"><path d="M22 12l-8 8 8 8" stroke="#fff" stroke-width="3" fill="none"/></svg></div>
<div class="abs hero-arrow" style="left:1164px"><svg width="36" height="40" viewBox="0 0 36 40"><path d="M14 12l8 8-8 8" stroke="#fff" stroke-width="3" fill="none"/></svg></div>

<svg class="abs catpanel" viewBox="0 0 287 486" width="287" height="486"><path d="M0 0H287V458L143 486 0 458z" fill="rgba(30,30,30,.86)"/></svg>
<ul class="abs catlist">
  <li><svg width="17" height="17" viewBox="0 0 20 20"><circle cx="10" cy="10" r="10" fill="#fff"/><path d="M5 10l3.5 3.5L15 7" stroke="#222" stroke-width="2.4" fill="none"/></svg>VASES</li>
  <li><svg width="17" height="17" viewBox="0 0 20 20"><circle cx="10" cy="10" r="10" fill="#fff"/><path d="M5 10l3.5 3.5L15 7" stroke="#222" stroke-width="2.4" fill="none"/></svg>THROW PILLOWS</li>
  <li><svg width="17" height="17" viewBox="0 0 20 20"><circle cx="10" cy="10" r="10" fill="#fff"/><path d="M5 10l3.5 3.5L15 7" stroke="#222" stroke-width="2.4" fill="none"/></svg>BLANKETS AND THROWS</li>
  <li><svg width="17" height="17" viewBox="0 0 20 20"><circle cx="10" cy="10" r="10" fill="#fff"/><path d="M5 10l3.5 3.5L15 7" stroke="#222" stroke-width="2.4" fill="none"/></svg>FOR YOUR FLOORS</li>
  <li><svg width="17" height="17" viewBox="0 0 20 20"><circle cx="10" cy="10" r="10" fill="#fff"/><path d="M5 10l3.5 3.5L15 7" stroke="#222" stroke-width="2.4" fill="none"/></svg>FOR YOUR WALLS</li>
  <li><svg width="17" height="17" viewBox="0 0 20 20"><circle cx="10" cy="10" r="10" fill="#fff"/><path d="M5 10l3.5 3.5L15 7" stroke="#222" stroke-width="2.4" fill="none"/></svg>FOR YOUR TABLE</li>
  <li><svg width="17" height="17" viewBox="0 0 20 20"><circle cx="10" cy="10" r="10" fill="#fff"/><path d="M5 10l3.5 3.5L15 7" stroke="#222" stroke-width="2.4" fill="none"/></svg>FOR YOUR BEDSIDE</li>
  <li><svg width="17" height="17" viewBox="0 0 20 20"><circle cx="10" cy="10" r="10" fill="#fff"/><path d="M5 10l3.5 3.5L15 7" stroke="#222" stroke-width="2.4" fill="none"/></svg>LET THERE BE LIGHT</li>
  <li><svg width="17" height="17" viewBox="0 0 20 20"><circle cx="10" cy="10" r="10" fill="#fff"/><path d="M5 10l3.5 3.5L15 7" stroke="#222" stroke-width="2.4" fill="none"/></svg>PUT YOUR FEET UP</li>
</ul>

<h1 class="abs hero-title">LUMORA HOME GOODS</h1>
<div class="abs hero-sub">At vero eos et accusamus et iusto odio dignis</div>
<a class="abs hero-btn" href="#">SHOP NOW!</a>

<div class="abs categories">
  <svg width="16" height="14" viewBox="0 0 16 14"><rect width="16" height="2.5" fill="#fff"/><rect y="5.7" width="16" height="2.5" fill="#fff"/><rect y="11.5" width="16" height="2.5" fill="#fff"/></svg>CATEGORIES
</div>
<a class="abs mainnav active" style="left:470px" href="#">HOME</a>
<a class="abs mainnav" style="left:560px" href="#">ABOUT LUMORA</a>
<a class="abs mainnav" style="left:711px" href="#">HOW DOES THIS CRAZINESS WORK?</a>
<a class="abs mainnav" style="left:1025px" href="#">CONTACT</a>

<!-- products -->
<h2 class="abs section-title">OUR PRODUCTS</h2>

<div class="abs product" style="left:98px;top:843px">
  <div class="photo"><div class="fill" role="img" aria-label="Folded blue plaid blankets" style="background:linear-gradient(135deg,#3d7cc4,#9cc3e6 60%,#7b8a5a)"></div></div>
  <h3>FINIBUS BONO RUM</h3><p>At vero eos et accusamus et iusto odio dignissimos duci anditii</p>
  <div class="meta"><span class="price">$234.00</span><span class="stars">★★★★☆</span></div>
</div>
<div class="abs product" style="left:355px;top:843px">
  <div class="photo hover"><div class="fill" role="img" aria-label="Glass vase with green leaves" style="background:linear-gradient(180deg,#3f6f7a,#5e8fb8)"></div>
    <div class="hover-icons">
      <span><svg width="16" height="16" viewBox="0 0 24 24"><circle cx="10" cy="10" r="7" stroke="#fff" stroke-width="3" fill="none"/><path d="M15 15l7 7" stroke="#fff" stroke-width="3"/></svg></span>
      <span><svg width="16" height="15" viewBox="0 0 24 22"><path d="M12 21L2 11a5.5 5.5 0 0 1 10-7 5.5 5.5 0 0 1 10 7z" fill="#fff"/></svg></span>
      <span><svg width="16" height="15" viewBox="0 0 34 32"><path d="M1 3h6l4 18h18l4-13H9" stroke="#fff" stroke-width="3" fill="none"/><circle cx="13" cy="27" r="3" fill="#fff"/><circle cx="27" cy="27" r="3" fill="#fff"/></svg></span>
    </div>
  </div>
  <h3>FINIBUS BONO RUM</h3><p>At vero eos et accusamus et iusto odio dignissimos duci anditii</p>
  <div class="meta"><span class="price">$234.00</span><span class="stars">★★★★☆</span></div>
</div>
<div class="abs product" style="left:613px;top:843px">
  <div class="photo"><div class="fill" role="img" aria-label="Stack of orange, red and green cushions" style="background:linear-gradient(180deg,#f0a060,#d8281e 50%,#a8c05a)"></div></div>
  <h3>FINIBUS BONO RUM</h3><p>At vero eos et accusamus et iusto odio dignissimos duci anditii</p>
  <div class="meta"><span class="price">$234.00</span><span class="stars">★★★★☆</span></div>
</div>
<div class="abs product" style="left:870px;top:843px">
  <div class="photo"><div class="fill" role="img" aria-label="Round dark wood pedestal table" style="background:linear-gradient(180deg,#4a2a22,#6b3a2c)"></div></div>
  <h3>FINIBUS BONO RUM</h3><p>At vero eos et accusamus et iusto odio dignissimos duci anditii</p>
  <div class="meta"><span class="price">$234.00</span><span class="stars">★★★★☆</span></div>
</div>

<div class="abs product" style="left:98px;top:1288px">
  <div class="photo"><div class="fill" role="img" aria-label="Rolled beige woven rug" style="background:linear-gradient(135deg,#c8b595,#8e7a5c)"></div></div>
  <h3>FINIBUS BONO RUM</h3><p>At vero eos et accusamus et iusto odio dignissimos duci anditii</p>
  <div class="meta"><span class="price">$234.00</span><span class="stars">★★★★☆</span></div>
</div>
<div class="abs product" style="left:355px;top:1288px">
  <div class="photo"><div class="fill" role="img" aria-label="Pink peonies in a glass vase" style="background:linear-gradient(180deg,#e27aa6,#f3c0d3 60%,#cfe0d0)"></div></div>
  <h3>FINIBUS BONO RUM</h3><p>At vero eos et accusamus et iusto odio dignissimos duci anditii</p>
  <div class="meta"><span class="price">$234.00</span><span class="stars">★★★★☆</span></div>
</div>
<div class="abs product" style="left:613px;top:1288px">
  <div class="photo"><div class="fill" role="img" aria-label="Blue and white striped bedding" style="background:linear-gradient(135deg,#4fa2d6,#d9ecf7 55%,#3b93cc)"></div></div>
  <h3>FINIBUS BONO RUM</h3><p>At vero eos et accusamus et iusto odio dignissimos duci anditii</p>
  <div class="meta"><span class="price">$234.00</span><span class="stars">★★★★☆</span></div>
</div>
<div class="abs product" style="left:870px;top:1288px">
  <div class="photo"><div class="fill" role="img" aria-label="Carved wooden nightstand" style="background:linear-gradient(180deg,#8a4a2a,#5e2f1a)"></div></div>
  <h3>FINIBUS BONO RUM</h3><p>At vero eos et accusamus et iusto odio dignissimos duci anditii</p>
  <div class="meta"><span class="price">$234.00</span><span class="stars">★★★★☆</span></div>
</div>

<a class="abs more-btn" href="#">VIEW MORE PRODUCTS</a>

<!-- promos -->
<div class="abs promo" style="left:0;width:387px">
  <div class="art" role="img" aria-label="Pink flowers in a white jug against a pale blue wall" style="background:linear-gradient(90deg,#e98aa0 0%,#cfe6ef 35%,#bcdde9 100%)"></div>
  <div class="copy" style="left:188px;top:38px"><div class="big">BIG SALE</div><div class="small">UP TO 50% OFF</div><span class="btn">SHOP NOW!</span></div>
</div>
<div class="abs promo" style="left:407px;width:386px">
  <div class="art" role="img" aria-label="Stacked white cushions on pale wood" style="background:linear-gradient(90deg,#cfcac2 0%,#eeece8 40%,#f3f1ed 100%)"></div>
  <div class="copy" style="left:172px;top:48px;text-align:center"><div class="mid" style="font-style:italic">NEW ARRIVALS</div><div style="font-size:15px;color:#222;margin-top:2px">At vero eoset accus ser</div><span class="btn" style="margin-top:14px">SHOP NOW!</span></div>
</div>
<div class="abs promo" style="left:813px;width:387px">
  <div class="art" role="img" aria-label="Stack of colourful folded knit throws" style="background:linear-gradient(90deg,#b0524a 0%,#6a6a8a 25%,#d9a06a 45%,#ecebe6 60%,#e4e1da 100%)"></div>
  <div class="copy" style="left:198px;top:38px"><div class="big">SALE</div><div class="small">UP TO 50% OFF</div><span class="btn">SHOP NOW!</span></div>
</div>

<!-- footer -->
<div class="abs fcol" style="left:100px"><h4>Information</h4><ul><li>About Us</li><li>Careers</li><li>Privacy &amp; Security</li><li>Site Map</li><li>Terms of Use</li><li>Blog</li></ul></div>
<div class="abs fdivider" style="left:258px"></div>
<div class="abs fcol" style="left:303px"><h4>Help &amp; support</h4><ul><li>Recommended Reading</li><li>Submit your Story</li><li>Contact Us</li><li>Frequently Asked Questions</li><li>How to Order</li></ul></div>
<div class="abs fdivider" style="left:507px"></div>
<div class="abs fcol" style="left:552px"><h4>My Account</h4><ul><li>Delivery Information</li><li>My Account</li><li>Order Tracking</li><li>Reminder Service</li><li>Shipping, Returns &amp; Fees</li></ul></div>
<div class="abs fdivider" style="left:733px"></div>
<div class="abs fcol newsletter" style="left:778px">
  <h4>Email Subscription</h4>
  <p>Register your email address to get information about us</p>
  <div class="subscribe"><div class="field">Email Address</div><div class="go">SUBSCRIBE</div></div>
  <h5>Stay Connected</h5>
  <div class="social-foot" role="img" aria-label="Social network links"><span></span><span></span><span></span><span></span><span></span><span></span><span></span><span></span></div>
</div>

<div class="abs bottomline"></div>
<div class="abs copyright">Copyrights © 2017, Lumora. All Rights Reserved &nbsp;| &nbsp; Privacy Policy | Terms of Use | Feedback</div>
<div class="abs payments" aria-label="Accepted payments"><span>Cardex</span><span>Vantra</span><span>Amerigo</span><span>Findly</span><span>Monvex</span></div>

</body>
</html>
```